Upmarket Dessert Lounge needs a Business Card Design

We are an upmarket dessert lounge needing a business card to match our image.

We want something that is simple yet beautiful, feminine, classy, sophisticated and elegant. We want it to stand out and don't mind if it is bold.

The design should include our logo and colours of red or maroon with gold highlights. We don't mind if black is used.

Marlow & Quince

Target Market(s)

For those who like to indulge or treat themselves and give in to their temptations on good quality desserts.

Industry/Entity Type

Business

Requirements
Must have
• Must include our logo and our name

Marlow & Quince

M & Q

```html
<!DOCTYPE html>
<html lang="en">
<head>
<meta charset="utf-8">
<title>Marlow &amp; Quince — Business Card</title>
<link rel="stylesheet" href="https://fonts.googleapis.com/css2?family=Arimo:wght@400;700&display=swap">
<style>
  :root {
    --stage: #e9e5e1;
    --card: #2a1f1d;
    --maroon: #8e1c1a;
    --maroon-deep: #5e100f;
    --gold: #e2b66d;
    --cream: #f3d7a6;
    --ink-light: #f4ede4;
  }
  * { box-sizing: border-box; margin: 0; padding: 0; }
  html, body { width: 1200px; height: 951px; overflow: hidden; }
  body {
    background: var(--stage);
    font-family: "Arimo", Arial, sans-serif;
    display: flex;
    flex-direction: column;
    align-items: center;
    justify-content: center;
    gap: 34px;
  }
  .card {
    position: relative;
    width: 720px;
    height: 411px;
    background: var(--card);
    border-radius: 22px;
    overflow: hidden;
    box-shadow: 0 10px 30px rgba(0,0,0,.25);
  }
  .card-art { position: absolute; inset: 0; width: 100%; height: 100%; }

  /* front */
  .front .edge {
    position: absolute; top: 0; bottom: 0; width: 26px;
    background: linear-gradient(90deg, var(--maroon-deep), var(--maroon) 60%, var(--maroon-deep));
  }
  .front .edge-left { left: 0; }
  .front .edge-right { right: 0; }
  .brand-name {
    position: absolute;
    color: var(--gold);
    font-weight: 700;
    letter-spacing: 2px;
    white-space: nowrap;
  }
  .front .brand-name {
    top: 130px; left: 0; right: 0; text-align: center;
    font-size: 44px;
  }
  .front .website {
    position: absolute; top: 300px; left: 0; right: 0; text-align: center;
    color: var(--gold); font-size: 20px; letter-spacing: 3px;
  }

  /* back */
  .back .brand-name {
    top: 62px; left: 150px; font-size: 30px;
  }
  .back .trading-name {
    position: absolute; top: 112px; right: 70px;
    color: var(--gold); font-size: 24px; letter-spacing: 1px;
  }
  .back .trading-name .amp { color: var(--ink-light); }
  .contact-list {
    position: absolute; left: 60px; top: 268px;
    list-style: none; color: var(--ink-light); font-size: 19px; line-height: 26px;
  }
  .contact-list li { display: flex; align-items: center; gap: 10px; }
  .contact-list svg { width: 16px; height: 16px; fill: var(--cream); flex: none; }
  .address {
    position: absolute; left: 415px; top: 294px;
    color: var(--ink-light); font-size: 19px; line-height: 26px;
    font-style: normal;
  }
  .address .line-first { display: flex; align-items: center; gap: 10px; margin-left: -26px; }
  .address svg { width: 16px; height: 16px; fill: var(--cream); }
</style>
</head>
<body>

  <section class="card front" aria-label="Card front">
    <div class="edge edge-left"></div>
    <div class="edge edge-right"></div>
    <div class="brand-name">Marlow &amp; Quince</div>
    <div class="website">www.marlowquince.com</div>
  </section>

  <section class="card back" aria-label="Card back">
    <svg class="card-art" viewBox="0 0 720 411" preserveAspectRatio="none" aria-hidden="true">
      <path d="M0 0 H200 C130 20 50 60 0 120 Z" fill="var(--maroon)"/>
      <path d="M0 105 C55 50 125 18 200 0 H214 C135 24 58 66 0 130 Z" fill="var(--cream)"/>
      <path d="M720 411 H560 C620 385 680 340 720 270 Z" fill="var(--maroon)"/>
      <path d="M720 285 C690 345 630 390 560 411 H540 C615 385 685 335 720 255 Z" fill="var(--cream)"/>
    </svg>

    <div class="brand-name">Marlow &amp; Quince</div>
    <div class="trading-name">Marlow <span class="amp">&amp;</span> Quince</div>

    <ul class="contact-list">
      <li><svg viewBox="0 0 16 16"><path d="M3 1l3 1 1 3-2 1.5a9 9 0 004.5 4.5L11 9l3 1 1 3-2 2C7 15 1 9 1 3z"/></svg>555-014-2290</li>
      <li><svg viewBox="0 0 16 16"><rect x="3" y="1" width="10" height="5"/><rect x="1" y="6" width="14" height="6" rx="1"/><rect x="4" y="10" width="8" height="5"/></svg>555-014-2291</li>
      <li><svg viewBox="0 0 16 16"><path d="M1 4h14v9H1z M1 4l7 5 7-5" fill="none" stroke="var(--cream)" stroke-width="1.6"/></svg>info@marlowquince.com</li>
      <li><svg viewBox="0 0 16 16"><circle cx="8" cy="8" r="7"/></svg>www.marlowquince.com</li>
    </ul>

    <address class="address">
      <span class="line-first"><svg viewBox="0 0 16 16"><path d="M8 1l7 7h-2v7H9v-4H7v4H3V8H1z"/></svg>1480 Linden Row</span>
      Suite 204-118<br>
      Harlow, TX 78114
    </address>
  </section>

</body>
</html>
```